Heron Loan Partners Business Card

We need a business card design for our mortgage servicing company. In addition to servicing the loans of homeowners, we help homeowners with purchasing their homes and any mortgage refinancing. We would like to see designs that use the colors in the logo attached below (gold-ish yellow and navy blue), and any other design you deem fit! The design should communicate a simpler life with smart mortgages provided by Heron.

```html
<!DOCTYPE html>
<html lang="en">
<head>
<meta charset="UTF-8">
<title>Heron Loan Partners Business Card</title>
<link href="https://fonts.googleapis.com/css2?family=Montserrat:wght@400;500;700;800&display=swap" rel="stylesheet">
<style>
  :root {
    --navy: #231f5c;
    --gold: #e0b43a;
    --ink: #1a1a1a;
    --paper: #ffffff;
    --backdrop: #5b5b5b;
  }
  html, body {
    margin: 0;
    width: 1200px;
    height: 900px;
    overflow: hidden;
    background: var(--backdrop);
    font-family: "Montserrat", sans-serif;
  }
  .canvas {
    position: relative;
    width: 1200px;
    height: 900px;
  }
  .card {
    position: absolute;
    left: 250px;
    width: 700px;
    height: 400px;
    background: var(--paper);
    overflow: hidden;
    box-shadow: 0 10px 24px rgba(0,0,0,.35);
  }
  .card-front { top: 36px; }
  .card-back { top: 464px; }

  .brand {
    position: absolute;
    display: flex;
    align-items: center;
    gap: 14px;
    color: var(--navy);
    font-weight: 800;
    white-space: nowrap;
  }
  .brand-dot {
    border-radius: 50%;
    background: var(--gold);
    flex: none;
  }
  .card-front .brand {
    left: 0; right: 0; top: 170px;
    justify-content: center;
    font-size: 40px;
  }
  .card-front .brand-dot { width: 34px; height: 34px; }
  .card-back .brand {
    right: 48px; top: 58px;
    font-size: 24px;
  }
  .card-back .brand-dot { width: 22px; height: 22px; }

  .holder {
    position: absolute;
    left: 0; top: 112px;
  }
  .holder-bar {
    position: absolute;
    left: 30px; top: 22px;
    width: 16px; height: 40px;
    background: var(--gold);
  }
  .holder-name {
    position: absolute;
    left: 60px; top: 0;
    margin: 0;
    font-size: 22px;
    font-weight: 800;
    letter-spacing: .5px;
    color: var(--navy);
    white-space: nowrap;
  }
  .holder-name .surname { color: var(--gold); }
  .holder-role {
    position: absolute;
    left: 66px; top: 32px;
    margin: 0;
    font-size: 18px;
    color: var(--ink);
  }

  .address {
    position: absolute;
    right: 40px; top: 190px;
    margin: 0;
    text-align: right;
    font-size: 17px;
    line-height: 1.4;
    font-style: normal;
    color: var(--ink);
  }

  .contacts {
    position: absolute;
    left: 200px; top: 236px;
    margin: 0; padding: 0;
    list-style: none;
    font-size: 16px;
    color: var(--ink);
  }
  .contacts li {
    display: flex;
    align-items: center;
    gap: 10px;
    height: 27px;
  }
  .contacts svg { width: 18px; height: 18px; fill: var(--gold); flex: none; }

  .bands { position: absolute; left: 0; top: 0; width: 700px; height: 400px; }

  .reg {
    position: absolute;
    left: 496px; top: 324px;
    margin: 0;
    font-size: 16px;
    font-weight: 500;
    color: var(--paper);
    white-space: nowrap;
  }
</style>
</head>
<body>
<main class="canvas">

  <section class="card card-front" aria-label="Card front">
    <div class="brand"><span class="brand-dot"></span>Heron Loan Partners</div>
  </section>

  <section class="card card-back" aria-label="Card back">
    <svg class="bands" viewBox="0 0 700 400" aria-hidden="true">
      <polygon points="0,352 444,352 441,360 0,360" fill="var(--gold)"/>
      <polygon points="0,368 436,368 426,400 0,400" fill="var(--navy)"/>
      <polygon points="470,300 700,300 700,400 440,400" fill="var(--gold)"/>
    </svg>

    <div class="brand"><span class="brand-dot"></span>Heron Loan Partners</div>

    <div class="holder">
      <span class="holder-bar"></span>
      <h1 class="holder-name">DANA <span class="surname">WHITFIELD</span></h1>
      <p class="holder-role">Owner</p>
    </div>

    <address class="address">4820 Alder Bend Rd, Ste<br>210, Fairview, TX 75069</address>

    <ul class="contacts">
      <li>
        <svg viewBox="0 0 24 24"><path d="M6.6 10.8a15 15 0 0 0 6.6 6.6l2.2-2.2a1 1 0 0 1 1-.25 11.4 11.4 0 0 0 3.6.57 1 1 0 0 1 1 1V20a1 1 0 0 1-1 1A17 17 0 0 1 3 4a1 1 0 0 1 1-1h3.5a1 1 0 0 1 1 1c0 1.25.2 2.45.57 3.57a1 1 0 0 1-.25 1z"/></svg>
        555.014.2297
      </li>
      <li>
        <svg viewBox="0 0 24 24"><path d="M2 5h20v14H2zm2 2v.5l8 5 8-5V7l-8 5z"/></svg>
        info@heronloanpartners.com
      </li>
      <li>
        <svg viewBox="0 0 24 24"><circle cx="12" cy="12" r="10"/></svg>
        www.heronloanpartners.com
      </li>
    </ul>

    <p class="reg">Reg Number: 480317</p>
  </section>

</main>
</body>
</html>
```